Hello my name is Colin, I am Starting a business called Lumen Wellness and fitness and am in need of a memorable business card.
It is a personal training studio. I have added the logo that i would like to be on the left center om my business card. i would like room left up the top for a heading sentence such as. "Is your body shocking for all the wrong reasons". there must be room left on the right of the logo below the main heading for 3 sub headings.
then under those 3 headings and logo room for another larger heading eg. "give me a call and learn how to eat chocolate, drink bear and have great sex". in what room is left i would like to be used for my contact details, use I'm Colin Ferrante your fitness expert on the left then on the right Phone, Email and website space in at least 12 Point. Very specific i know :) now onto the back, for the back i would like an eye catching graphic and room for one main headline and 3 bullet points centered just write anything i will choose what to put in them when i pick a winner. Thank you very much for sticking through all of that :) i appreciate you taking the time to read it and hopefully undergo designing me a business card.
I can't wait to see the designs!

Target Market(s)

slightly more towards females although it would probably be best if it was targeted towards both sexes

Industry/Entity Type

Training

Requirements
Nice to have
• I would love to see if anyone could come up with a design that would really make my card stand out and be memorable.
Should not have
• tacky fitness photos of abs and muscles etc.

```html
<!DOCTYPE html>
<html lang="en">
<head>
<meta charset="utf-8">
<title>Lumen Wellness and Fitness – Business Card</title>
<link rel="stylesheet" href="https://fonts.googleapis.com/css2?family=Questrial&family=Open+Sans:wght@400&display=swap">
<style>
  :root {
    --stage: #e9e6e2;
    --card: #ffffff;
    --brand-blue: #1e4a7e;
    --brand-deep: #143862;
    --ink: #2b2b2b;
    --ink-soft: #444444;
    --strip-grey: #333333;
    --label: #1a1a1a;
    --card-shadow: 0 4px 14px rgba(0,0,0,0.28);
  }
  * { margin: 0; padding: 0; box-sizing: border-box; }
  html, body { width: 1200px; height: 788px; overflow: hidden; }
  body {
    background: var(--stage);
    font-family: "Questrial", "Century Gothic", sans-serif;
    position: relative;
  }
  .side-label {
    position: absolute;
    font-size: 21px;
    color: var(--label);
    transform: translateX(-50%);
    white-space: nowrap;
  }
  .card {
    position: absolute;
    width: 525px;
    height: 300px;
    background: var(--card);
    border-radius: 20px;
    overflow: hidden;
    box-shadow: var(--card-shadow);
  }
  .card > * { position: absolute; }

  .tagline {
    left: 0; right: 0;
    text-align: center;
    font-size: 13px;
    color: var(--ink);
  }

  .brand { color: var(--brand-blue); line-height: 1; }
  .brand-name { display: block; font-size: 64px; letter-spacing: -1px; }
  .brand-sub { display: block; font-size: 17px; text-align: right; margin-top: 2px; }

  /* Front */
  .card-front { left: 338px; top: 73px; }
  .card-front .tagline { top: 24px; }
  .card-front .brand { left: 50px; top: 86px; width: 210px; }
  .owner { left: 312px; top: 84px; color: var(--brand-blue); }
  .owner-name { font-size: 17px; letter-spacing: 0.3px; }
  .owner-role { font-size: 13px; margin-top: 3px; }
  .pitch { left: 312px; top: 180px; font-size: 12.5px; line-height: 16.5px; color: var(--brand-blue); }
  .phone { left: 50px; top: 211px; font-size: 13.5px; color: var(--ink-soft); letter-spacing: 0.3px; }
  .phone b, .web-lines b { font-style: italic; font-weight: 700; font-family: "Open Sans", sans-serif; font-size: 12px; margin-right: 6px; }
  .front-bands { left: 0; top: 0; width: 525px; height: 300px; }
  .web-lines { left: 312px; top: 252px; color: #fff; font-size: 12.5px; line-height: 18px; letter-spacing: 0.3px; }

  /* Back 1 */
  .card-back-one { left: 54px; top: 446px; }
  .figure-art {
    left: 42px; top: 18px; width: 146px; height: 266px;
    background: linear-gradient(180deg, var(--brand-deep), var(--brand-blue));
    border-radius: 60px 60px 12px 12px;
    opacity: 0.95;
  }
  .card-back-one .brand { left: 255px; top: 22px; width: 126px; }
  .card-back-one .brand-name { font-size: 38px; }
  .card-back-one .brand-sub { font-size: 10px; }
  .points { left: 258px; top: 116px; list-style: none; font-family: "Open Sans", sans-serif; font-size: 16px; color: #111; }
  .points li { position: relative; padding-left: 25px; height: 33px; }
  .points li:last-child { margin-top: 3px; }
  .points li::before { content: ""; position: absolute; left: 0; top: 8px; width: 6px; height: 6px; background: #111; }
  .card-back-one .site { left: 256px; top: 253px; font-size: 19px; color: var(--ink); letter-spacing: 0.5px; }

  /* Back 2 */
  .card-back-two { left: 621px; top: 441px; }
  .card-back-two .tagline { top: 20px; }
  .card-back-two .brand { left: 104px; top: 84px; width: 312px; }
  .card-back-two .brand-name { font-size: 104px; letter-spacing: -2px; }
  .card-back-two .brand-sub { font-size: 24px; margin-top: 4px; }
  .card-back-two .site { left: 0; right: 0; top: 253px; text-align: center; font-size: 19px; color: var(--ink); letter-spacing: 4px; }
</style>
</head>
<body>
  <span class="side-label" style="left:600px; top:34px;">Front</span>
  <span class="side-label" style="left:324px; top:404px;">Back - 1</span>
  <span class="side-label" style="left:897px; top:404px;">Back - 2</span>

  <section class="card card-front">
    <svg class="front-bands" viewBox="0 0 525 300" aria-hidden="true">
      <defs>
        <linearGradient id="bandBlue" x1="0" y1="0" x2="1" y2="0">
          <stop offset="0" stop-color="#1e4a7e"/>
          <stop offset="1" stop-color="#17406f"/>
        </linearGradient>
      </defs>
      <polygon points="0,273 258,273 246,288 0,288" fill="#333333"/>
      <polygon points="292,247 525,247 525,300 0,300 0,291 256,291" fill="url(#bandBlue)"/>
    </svg>
    <p class="tagline">Is your body shocking for all the wrong reasons</p>
    <div class="brand">
      <span class="brand-name">Lumen</span>
      <span class="brand-sub">Wellness and Fitness</span>
    </div>
    <div class="owner">
      <p class="owner-name">Colin Ferrante</p>
      <p class="owner-role">Your Fitness Expert</p>
    </div>
    <p class="pitch">Give me a call and learn<br>how to eat chocolate<br>drink bear and have great sex</p>
    <p class="phone"><b>p</b>: +12 345 67890</p>
    <p class="web-lines"><b>e</b>: info@website.com<br><b>w</b>: www.website.com</p>
  </section>

  <section class="card card-back-one">
    <div class="figure-art" role="img" aria-label="Illustration area: blue silhouettes of a man in a suit and a woman standing side by side"></div>
    <div class="brand">
      <span class="brand-name">Lumen</span>
      <span class="brand-sub">Wellness and Fitness</span>
    </div>
    <ul class="points">
      <li>Lorem Ipsum has been ...</li>
      <li>Lorem Ipsum has been ...</li>
      <li>Lorem Ipsum has been ...</li>
    </ul>
    <p class="site">www.website.com</p>
  </section>

  <section class="card card-back-two">
    <p class="tagline">Is your body shocking for all the wrong reasons</p>
    <div class="brand">
      <span class="brand-name">Lumen</span>
      <span class="brand-sub">Wellness and Fitness</span>
    </div>
    <p class="site">www.website.com</p>
  </section>
</body>
</html>
```